IT consulting company looking for a modern business design for a website and a new logo

We are the IT-consulting company VelmaTrix from Germany and need a new and modern business website and a new logo. We are specialized in output management. Our services include business analysis, outsourcing, development, training and project leading. We wish for a design with nature pictures (mountains, lakes, rivers, forests, etc.) for our company with the colors green and blue. If it is possible, a slow-mo video of a nature scene. The design should be responsive and the menu should change to a hamburger menu. The following are: • Services / Solutions 1. Output Management 2. Outsourcing 3. Development 4. Business Analyst 5. Training • Partners • Careers • About Us 1. Project A 2. Project B 3. Project C • Contact Notes for the following categories: For "Services / Solutions" we want to conclude some contents from all the sub-points and sub-points below. Additionally, we would like to see some sub-point under "Services / Solutions". For Output Management: "5 Benefits of Output Management Systems (OMS) - OMS Simplifies and Accelerates External Communication - Helps Reduce Communication Mistakes - Provides Customers With Fast and Secure Responses to your questions - Employees can focus on the essential as they can access prepared templates - Companies get complete transparency about their communication "The point" partner does not have sub-points. The content here is a quote and the logo from the company Brel. For now, just placeholders on this site. The next point wants to be "career" without sub-point and wants to contain some text. Carrer options wants to be listed here. Next point wants to be "About us", where we need sub-points which we do not know exactly at this moment, but they will contain text. By clicking directly on "About us" we want to include pictures and texts about 6 employees for which we only need placeholders at the moment. The last point wants to be "contact", where customers can send us messages. The main page should include a story about our company, which can be a placeholder for now. For reference, designs have a look at: https://brelvanto.de/ https://www.tarnopix.com/ https://www.pldrive.de/ We prefer WordPress designs, created with the plugin ELEMENTOR, so that we can easily edit the content by ourselves. The final design should look professional, competent and modern.

Target Market(s)

With our website, we want to reach the following target groups. <br> <br> <br> <br> <br> <br> <br> <br> <br> <br> <br> <br> <br> <br> <br> <br> <br> <br> <br> <br> <br> <br> <br> <br> <br> <br> <br> <br> <br> <br> <br> <br> <br> <br> <br> <br> <br> <br> <br> <br> <br> <br> <br> <br> <br> <br> <br> <br> <br>

Industry/Entity Type

Consulting

Logo Text

(optionally) VelmaTrix

Font styles to use
Sans Serif

Colors

Designer to choose colors to be used in the design.

Requirements
Must have
• 1. Outsourcing 3. Development 4. Business Analyst 5. Training • Partners • Careers • About Us 1. Project A 2. Project B 3. Project C • Contact The above-mentioned background picture with nature motifs (mountains, lakes, rivers, forests, etc.). WordPress design in primary colors blue and green.
Nice to have
• ELEMENTOR template. Effects for the background pictures. Counter of all successful projects for Output Management, Business Analyst and Training

```html
<!DOCTYPE html>
<html lang="de">
<head>
<meta charset="utf-8">
<title>VelmaTrix – IT Consulting</title>
<link href="https://fonts.googleapis.com/css2?family=Poppins:wght@300;400;500;600;700&display=swap" rel="stylesheet">
<style>
:root{
  --blue:#1a5ca8;
  --blue-deep:#0f4f9f;
  --green:#7cbf2e;
  --text:#2b2b2b;
  --muted:#555;
  --line:#b9b9b9;
  --navy:#1c3150;
  --pale:#e7ebef;
}
*{box-sizing:border-box;margin:0;padding:0}
html,body{width:1200px;height:4295px;overflow:hidden}
body{font-family:'Poppins',sans-serif;color:var(--text);background:#fff;position:relative}
section,header,footer{position:absolute;left:0;width:1200px}
.abs{position:absolute}
.btn{position:absolute;background:var(--green);color:#fff;border-radius:20px;display:flex;align-items:center;justify-content:center;font-weight:500}
.title{position:absolute;left:0;width:1200px;text-align:center;font-weight:600;color:var(--blue)}
.title .g{color:var(--green)}
.rule{position:absolute;left:560px;width:80px;height:2px;background:var(--line)}

/* header */
.topbar{top:0;height:6px;background:#d6d6d6}
.site-header{top:6px;height:94px;background:#fff}
.brand{position:absolute;display:flex;align-items:center;gap:12px;font-weight:600;color:var(--blue)}
.brand .mark{border-radius:50%;border:3px solid var(--green)}
.nav{position:absolute;left:464px;top:42px;display:flex;gap:26px;font-size:14px;font-weight:500;color:#222}
.nav .active{color:var(--green)}
.phone{left:888px;top:36px;width:172px;height:32px;font-size:16px;gap:8px}

/* hero */
.hero{top:100px;height:553px;background:linear-gradient(90deg,#e9f1f9 0%,#dde8f3 40%,#b7c4d2 70%,#8d9cb0 100%)}
.hero h1{position:absolute;left:143px;top:148px;font-size:48px;line-height:64px;font-weight:600;color:var(--blue)}
.hero .btn{left:141px;top:353px;width:175px;height:40px;font-size:17px}

/* about */
.about{top:653px;height:430px}
.about .mission{position:absolute;top:156px;width:1200px;text-align:center;font-size:14px;font-weight:600;color:#111}
.about p.body{position:absolute;left:145px;top:184px;width:910px;text-align:center;font-size:14px;line-height:25.5px;color:#333}
.about .btn{left:530px;top:320px;width:138px;height:32px;font-size:16px}

/* services */
.services{top:1083px;height:447px;background:linear-gradient(180deg,#3e5a73 0%,#2f4a5e 45%,#2d4f3c 100%);overflow:hidden}
.services .title{color:#fff}
.svc-label{position:absolute;color:#fff;font-size:18px;font-weight:400}
.hub{position:absolute;left:433px;top:297px;width:300px;height:300px;border-radius:50%;background:#fff;border:5px solid var(--blue)}
.hub-name{position:absolute;left:433px;top:392px;width:300px;text-align:center;font-size:32px;font-weight:600;color:var(--blue)}
.node{position:absolute;width:72px;height:72px;border-radius:50%;background:#fff;border:3px solid var(--green)}
.node svg{position:absolute;left:18px;top:18px}
.dot{position:absolute;width:12px;height:12px;border-radius:50%;background:#fff;border:3px solid var(--green)}

/* vision */
.vision{top:1530px;height:633px}
.vcircle{position:absolute;border-radius:50%;text-align:center;background:radial-gradient(circle at 50% 40%,#fafafa 0%,#e4e4e4 100%)}
.vcircle h3{font-size:18px;font-weight:500;color:var(--blue)}
.vcircle .sub{font-size:12px;color:#333}
.vcircle p{font-size:13px;line-height:21px;color:#444;margin-top:18px}
.vcircle.center{background:var(--blue-deep);box-shadow:0 0 0 6px #fff,0 0 0 8px var(--blue-deep)}
.vcircle.center h3,.vcircle.center .sub,.vcircle.center p{color:#fff}
.vision .btn{left:517px;top:510px;width:166px;height:38px;font-size:17px}

/* OMS benefits */
.oms{top:2163px;height:534px;background:linear-gradient(180deg,#2b4660 0%,#324c52 55%,#3a5a3c 100%);overflow:hidden}
.oms h2{position:absolute;left:143px;top:100px;font-size:30px;font-weight:400;color:#fff;line-height:38px}
.oms h2 span{color:var(--green)}
.oms ul{position:absolute;left:143px;top:192px;list-style:none;width:560px}
.oms li{position:relative;padding-left:30px;font-size:14px;line-height:21px;color:#fff;margin-bottom:11.5px}
.oms li svg{position:absolute;left:0;top:3px}
.oms .btn{left:141px;top:384px;width:119px;height:39px;font-size:17px}

/* reviews */
.reviews{top:2697px;height:356px}
.review{position:absolute;top:165px;width:470px;height:110px}
.review .photo{position:absolute;left:0;top:0;width:103px;height:108px;background:linear-gradient(180deg,#c9d3dc,#8898a8)}
.review .q{position:absolute;left:116px;top:0;font-size:34px;line-height:30px;color:#bbb;font-family:Georgia,serif}
.review p{position:absolute;left:116px;top:28px;width:320px;font-size:13px;line-height:22px;color:#333}
.review p b{color:var(--blue);font-weight:500}
.review .who{position:absolute;left:116px;top:84px;font-size:14px;color:#222}
.arrow{position:absolute;width:36px;height:36px;border-radius:50%;background:#fff;box-shadow:0 1px 6px rgba(0,0,0,.25)}

/* team */
.team{top:3053px;height:577px;background:var(--pale)}
.member{position:absolute;top:158px;width:220px;text-align:center}
.member .photo{width:128px;height:128px;margin:0 auto;border-radius:50%;border:3px solid var(--blue);background:#fff;padding:4px}
.member .photo div{width:100%;height:100%;border-radius:50%;background:linear-gradient(180deg,#9aa5b0,#4a4f57)}
.member h4{margin-top:30px;font-size:16px;font-weight:500;color:var(--blue);line-height:18px}
.member .role{font-size:13px;color:#333;line-height:16px}
.member p{margin-top:12px;font-size:13px;line-height:21px;color:#444}
.team .btn{left:517px;top:464px;width:166px;height:38px;font-size:17px}

/* partners */
.partners{top:3630px;height:375px}
.partners .title{font-weight:400}
.pbox{position:absolute;top:167px;width:122px;height:73px;border:1px solid #ddd;background:#fff;box-shadow:0 1px 4px rgba(0,0,0,.08)}
.pbox span{position:absolute;left:31px;top:22px;width:60px;height:28px;border-radius:4px;background:#cfd8e2}
.pdot{position:absolute;top:268px;width:22px;height:22px;border-radius:50%;border:1px solid #bbb;background:#fff}

/* footer */
.site-footer{top:4005px;height:290px;background:linear-gradient(180deg,#223a5a,#1b2f4b);color:#fff}
.fcol{position:absolute;top:50px;font-size:12.5px;line-height:25px}
.fcol h5{font-size:14px;font-weight:400;color:var(--green);margin-bottom:16px}
.fcol .row{display:flex;gap:10px;align-items:flex-start;line-height:19px;margin-bottom:18px}
.email-input{width:192px;height:30px;border-radius:15px;background:#fff;color:#888;font-size:11px;padding-left:14px;display:flex;align-items:center;margin-top:8px}
.subscribe{position:relative;margin-top:8px;width:122px;height:30px;font-size:15px}
.social{display:flex;gap:12px}
.social span{width:24px;height:24px;border-radius:50%;background:#fff}
.copy{position:absolute;left:0;top:252px;width:1200px;text-align:center;font-size:12px;color:#ddd;border-top:1px solid rgba(255,255,255,.15);padding-top:10px}
</style>
</head>
<body>

<div class="abs topbar" style="left:0;width:1200px"></div>

<header class="site-header">
  <div class="brand" style="left:140px;top:30px;font-size:32px">
    <span class="mark" style="width:46px;height:46px"></span>VelmaTrix
  </div>
  <nav class="nav">
    <span class="active">Home</span><span>About Us</span><span>Services</span><span>Careers</span><span>Contact Us</span>
  </nav>
  <div class="btn phone">
    <svg width="16" height="16" viewBox="0 0 24 24"><path d="M6.6 10.8a15 15 0 0 0 6.6 6.6l2.2-2.2a1 1 0 0 1 1-.25 11.4 11.4 0 0 0 3.6.6 1 1 0 0 1 1 1V20a1 1 0 0 1-1 1A17 17 0 0 1 3 4a1 1 0 0 1 1-1h3.5a1 1 0 0 1 1 1c0 1.25.2 2.45.6 3.6a1 1 0 0 1-.25 1z" fill="none" stroke="#fff" stroke-width="2"/></svg>
    123.456.7890
  </div>
</header>

<section class="hero" role="img" aria-label="Photo of two business colleagues reviewing a tablet in a bright office">
  <h1>We Are Specialized<br>In Output<br>Management</h1>
  <div class="btn">We Can Help</div>
</section>

<section class="about">
  <h2 class="title" style="top:70px;font-size:40px;font-weight:600">About <span style="color:var(--blue)">Velma</span><span class="g">Trix</span></h2>
  <div class="rule" style="top:134px;width:126px;left:537px"></div>
  <div class="mission">Our mission is dipiscing elit, sed diam nonummy nibh euismod tincidunt ut.</div>
  <p class="body">Lorem ipsum dolor sit amet, consectetuer adipiscing elit, sed diam nonummy nibh euismod tincidunt ut laoreet dolore magna aliquam erat volutpat. Ut wisi enim ad minim veniam, quis nostrud exerci tation ullamcorper suscipit lobortis nisl ut aliquip ex ea commodo consequat. Duis autem vel eum iriure dolor in hendrerit in vulputate velit esse molestie consequat, vel illum dolore eu feugiat nulla facilisis at vero eros et accumsan et iusto odio dignissim qui blandit praesent luptatum zzril delenit augue duis dolore te feugait nulla facilisi.</p>
  <div class="btn">Read More</div>
</section>

<section class="services" role="img" aria-label="Background photo of forested mountains under a cloudy sky">
  <h2 class="title" style="top:68px;font-size:34px">Our <span class="g">Services</span></h2>
  <div class="svc-label" style="left:528px;top:150px">Entwicklung</div>
  <div class="svc-label" style="left:269px;top:260px">Outsourcing</div>
  <div class="svc-label" style="left:781px;top:256px">Business Analyst</div>
  <div class="svc-label" style="left:134px;top:363px">Output Management</div>
  <div class="svc-label" style="left:835px;top:359px">Schulungen</div>

  <div class="hub"></div>
  <div class="hub-name">VelmaTrix</div>

  <div class="dot" style="left:577px;top:287px"></div>
  <div class="dot" style="left:474px;top:324px"></div>
  <div class="dot" style="left:679px;top:324px"></div>
  <div class="dot" style="left:432px;top:396px"></div>
  <div class="dot" style="left:723px;top:396px"></div>

  <div class="node" style="left:547px;top:189px"><svg width="36" height="36" viewBox="0 0 36 36"><path d="M10 26l6-14 14-6-6 14z" fill="var(--blue)"/><circle cx="22" cy="22" r="6" fill="none" stroke="var(--green)" stroke-width="3"/></svg></div>
  <div class="node" style="left:393px;top:239px"><svg width="36" height="36" viewBox="0 0 36 36"><circle cx="18" cy="18" r="9" fill="none" stroke="var(--blue)" stroke-width="3"/><circle cx="18" cy="18" r="3" fill="var(--green)"/><path d="M18 3v6M18 27v6M3 18h6M27 18h6" stroke="var(--blue)" stroke-width="2"/></svg></div>
  <div class="node" style="left:697px;top:239px"><svg width="36" height="36" viewBox="0 0 36 36"><rect x="6" y="20" width="5" height="12" fill="var(--blue)"/><rect x="14" y="14" width="5" height="18" fill="var(--blue)"/><rect x="22" y="8" width="5" height="24" fill="var(--blue)"/><path d="M5 14l9-6 6 4 10-8" stroke="var(--green)" stroke-width="2" fill="none"/></svg></div>
  <div class="node" style="left:341px;top:339px"><svg width="36" height="36" viewBox="0 0 36 36"><rect x="4" y="6" width="24" height="18" rx="2" fill="none" stroke="var(--blue)" stroke-width="3"/><path d="M10 30h12" stroke="var(--blue)" stroke-width="3"/><rect x="22" y="14" width="10" height="16" fill="var(--green)"/></svg></div>
  <div class="node" style="left:756px;top:339px"><svg width="36" height="36" viewBox="0 0 36 36"><rect x="12" y="5" width="20" height="15" fill="none" stroke="var(--blue)" stroke-width="2.5"/><circle cx="8" cy="12" r="3" fill="var(--green)"/><path d="M8 16v14M4 22h10M22 20v10" stroke="var(--blue)" stroke-width="2.5"/></svg></div>
</section>

<section class="vision">
  <h2 class="title" style="top:84px;font-size:30px">Our <span class="g">Vision</span></h2>
  <div class="rule" style="top:132px"></div>

  <div class="vcircle" style="left:190px;top:183px;width:274px;height:274px;padding-top:50px">
    <svg width="60" height="56" viewBox="0 0 60 56"><circle cx="28" cy="26" r="14" fill="none" stroke="var(--blue)" stroke-width="3"/><path d="M38 36l12 12" stroke="var(--blue)" stroke-width="4"/><circle cx="28" cy="26" r="5" fill="var(--green)"/></svg>
    <h3>Discover</h3><div class="sub">Evaluate new geos</div>
    <p>Ut wisi enim ad minim veniam,<br>quis nostrud exerci tatio<br>Ut wisi enim ad minim.</p>
  </div>
  <div class="vcircle" style="left:728px;top:183px;width:274px;height:274px;padding-top:50px">
    <svg width="60" height="56" viewBox="0 0 60 56"><path d="M30 2v52" stroke="var(--blue)" stroke-width="3"/><path d="M12 12h36M18 22h24M8 32h44M16 42h28" stroke="var(--blue)" stroke-width="4"/><rect x="27" y="18" width="6" height="8" fill="var(--green)"/></svg>
    <h3>Align</h3><div class="sub">Ensure success</div>
    <p>Ut wisi enim ad minim veniam,<br>quis nostrud exerci tatio<br>Ut wisi enim ad minim.</p>
  </div>
  <div class="vcircle center" style="left:455px;top:175px;width:280px;height:280px;padding-top:50px">
    <svg width="60" height="56" viewBox="0 0 60 56"><path d="M6 6h12M6 6v12M54 6H42M54 6v12M6 50h12M6 50V38M54 50H42M54 50V38M8 8l14 14M52 8L38 22M8 48l14-14M52 48L38 34" stroke="#fff" stroke-width="3" fill="none"/></svg>
    <h3>Expand</h3><div class="sub">Set up new geos</div>
    <p>Ut wisi enim ad minim veniam, quis<br>nostrud exerci tatio<br>Ut wisi enim ad minim.</p>
  </div>
  <div class="btn">Call Us Today</div>
</section>

<section class="oms" role="img" aria-label="Background photo of a green valley with forest and mountains">
  <h2>5 Vorteile von<br><span>Output Management Systemen (OMS)</span></h2>
  <ul>
    <li><svg width="14" height="14" viewBox="0 0 14 14"><circle cx="7" cy="7" r="6" fill="none" stroke="var(--green)" stroke-width="1.5"/><path d="M4 7l2 2 4-4" stroke="var(--green)" stroke-width="1.5" fill="none"/></svg>OMS vereinfacht und beschleunigt die Kommunikation mit Außen.</li>
    <li><svg width="14" height="14" viewBox="0 0 14 14"><circle cx="7" cy="7" r="6" fill="none" stroke="var(--green)" stroke-width="1.5"/><path d="M4 7l2 2 4-4" stroke="var(--green)" stroke-width="1.5" fill="none"/></svg>Hilft dabei Fehler bei der Kommunikation zu reduzieren.</li>
    <li><svg width="14" height="14" viewBox="0 0 14 14"><circle cx="7" cy="7" r="6" fill="none" stroke="var(--green)" stroke-width="1.5"/><path d="M4 7l2 2 4-4" stroke="var(--green)" stroke-width="1.5" fill="none"/></svg>Kunden erhalten schnell und sicher antworten auf Ihre Fragen.</li>
    <li><svg width="14" height="14" viewBox="0 0 14 14"><circle cx="7" cy="7" r="6" fill="none" stroke="var(--green)" stroke-width="1.5"/><path d="M4 7l2 2 4-4" stroke="var(--green)" stroke-width="1.5" fill="none"/></svg>Mitarbeiter können sich auf das wesentliche konzentrieren, da sie auf vorbereitete Vorlagen zurückgreifen können.</li>
    <li><svg width="14" height="14" viewBox="0 0 14 14"><circle cx="7" cy="7" r="6" fill="none" stroke="var(--green)" stroke-width="1.5"/><path d="M4 7l2 2 4-4" stroke="var(--green)" stroke-width="1.5" fill="none"/></svg>Unternehmen erhalten vollständige Transparenz über Ihre Kommunikation</li>
  </ul>
  <div class="btn">Call Us Today</div>
  <div class="abs" style="left:708px;top:160px;width:290px;height:290px;border-radius:50%;background:var(--blue-deep)"></div>
  <div class="abs" role="img" aria-label="Photo of a smiling businesswoman with crossed arms" style="left:748px;top:68px;width:210px;height:410px;border-radius:100px 100px 20px 20px;background:linear-gradient(180deg,#7a5a45 0%,#c9a894 35%,#efe9e4 60%,#8a6a55 100%)"></div>
</section>

<section class="reviews">
  <h2 class="title" style="top:56px;font-size:34px">Happy Customer <span class="g">Reviews</span></h2>
  <div class="rule" style="top:118px"></div>
  <div class="arrow" style="left:82px;top:207px"></div>
  <div class="review" style="left:142px">
    <div class="photo" role="img" aria-label="Portrait photo of a customer"></div>
    <div class="q">&ldquo;</div>
    <p>Lorem ipsum dolor smet, consectetuer adipiscing elit, sed diam nonumtincidunt ut laoreet....<b>[+]</b></p>
    <div class="who">Lorem Ipsum</div>
  </div>
  <div class="review" style="left:612px">
    <div class="photo" role="img" aria-label="Portrait photo of a customer"></div>
    <div class="q">&ldquo;</div>
    <p>Lorem ipsum dolor smet, consectetuer adipiscing elit, sed diam nonumtincidunt ut laoreet....<b>[+]</b></p>
    <div class="who">Lorem Ipsum</div>
  </div>
  <div class="arrow" style="left:1063px;top:193px"></div>
</section>

<section class="team">
  <h2 class="title" style="top:80px;font-size:32px">Our <span class="g">Team</span></h2>
  <div class="rule" style="top:130px"></div>
  <div class="member" style="left:128px"><div class="photo" role="img" aria-label="Portrait photo of a team member"><div></div></div><h4>Hanna Leitner</h4><div class="role">Head of Operations</div><p>Ut wisi enim ad minim veniam,<br>quis nostrUt wisi enim a<br>nostrud exd minim.</p></div>
  <div class="member" style="left:363px"><div class="photo" role="img" aria-label="Portrait photo of a team member"><div></div></div><h4>Jonas Weidel</h4><div class="role">Product Lead</div><p>Ut wisi enim ad minim veniam,<br>quis nostrUt wisi enim a nostrud<br>exd minim.</p></div>
  <div class="member" style="left:600px"><div class="photo" role="img" aria-label="Portrait photo of a team member"><div></div></div><h4>Malik Osterholt</h4><div class="role">CEO</div><p>Ut wisi enim ad minim veniam,<br>quis nostrUt wisi enim a nostrud<br>exd minim.</p></div>
  <div class="member" style="left:837px"><div class="photo" role="img" aria-label="Portrait photo of a team member"><div></div></div><h4>Tobias Brenner</h4><div class="role">Co-Founder, Advisor</div><p>Ut wisi enim ad minim veniam,<br>quis nostrUt wisi enim a nostrud<br>exd minim.</p></div>
  <div class="btn">Meet Our Team</div>
</section>

<section class="partners">
  <h2 class="title" style="top:80px;font-size:30px">Our <span>Partners</span></h2>
  <div class="pbox" style="left:162px"><span></span></div>
  <div class="pbox" style="left:310px"><span></span></div>
  <div class="pbox" style="left:458px"><span></span></div>
  <div class="pbox" style="left:606px"><span></span></div>
  <div class="pbox" style="left:754px"><span style="border-radius:50%;left:41px;top:16px;width:40px;height:40px"></span></div>
  <div class="pbox" style="left:900px"><span></span></div>
  <div class="pdot" style="left:539px"></div>
  <div class="pdot" style="left:572px"></div>
</section>

<footer class="site-footer">
  <div class="fcol" style="left:143px">
    <h5>Quick Links</h5>
    <div>Home</div><div>About Us</div><div>Services</div><div>Careers</div><div>Contact Us</div>
  </div>
  <div class="fcol" style="left:303px">
    <h5>Contact Details</h5>
    <div class="row"><svg width="14" height="16" viewBox="0 0 14 16"><path d="M7 15s5-5 5-9A5 5 0 0 0 2 6c0 4 5 9 5 9z" fill="var(--green)"/><circle cx="7" cy="6" r="2" fill="#1c3150"/></svg><span>Street Name, City Name<br>State Zipcode</span></div>
    <div class="row"><svg width="14" height="14" viewBox="0 0 24 24"><circle cx="12" cy="12" r="10" fill="none" stroke="var(--green)" stroke-width="2"/><path d="M8 8l2 0 1 3-1 1a6 6 0 0 0 3 3l1-1 3 1v2a8 8 0 0 1-9-9z" fill="var(--green)"/></svg><span>123.456.7890</span></div>
    <div class="row"><svg width="16" height="12" viewBox="0 0 16 12"><rect x="1" y="1" width="14" height="10" fill="none" stroke="var(--green)" stroke-width="1.5"/><path d="M1 1l7 6 7-6" stroke="var(--green)" stroke-width="1.5" fill="none"/></svg><span>inquiry@velmatrix.com</span></div>
  </div>
  <div class="fcol" style="left:580px">
    <h5>Newsletter Signup</h5>
    <div style="line-height:19px">Lorem Ispum is the dummy<br>text of the industry</div>
    <div class="email-input">enter email address</div>
    <div class="btn subscribe">Subscribe</div>
  </div>
  <div class="fcol" style="left:853px">
    <h5>Follow Us On</h5>
    <div class="social"><span></span><span></span><span></span></div>
    <div class="brand" style="position:relative;margin-top:28px;font-size:28px;color:#fff">
      <span class="mark" style="width:40px;height:40px;border-color:#fff"></span>VelmaTrix
    </div>
  </div>
  <div class="copy">Copyright © 2019 VelmaTrix. All Rights Reserved.</div>
</footer>

</body>
</html>
```